Mara Penrith Copywriter Website

I am starting a new business as a freelance copywriter. Trying to set up the website for my business is proving to be too technical for me. I would like a simple, clean website using primarily black and white. I have attached the logo I would like used. I would like the menu icons to be Home, Services, Portfolio, Blog, Contact. I would like my mobile phone number (0412 583 906) and email address (mara.penrith.copywriter@fernmail.test) used in the header of the site. I need the site to be easily manageable and inter-changeable for me to be able to move things around and add images, etc with ease.

I would like the home page to be a static page with space for an image of myself somewhere (I haven't had this taken as yet), an area to put a bit about myself and my business, and also somewhere to include social media icons/links. Again, I would like the whole website and home page to be easily managed so that I can add/delete things with ease.

I would like the image of the typewriter used in the website somewhere also please.

Coding

Coded - Design and coding required

Number of Pages Required

5+ page

Font styles to use
Sans Serif
Script

Colors
fdf0f6

Requirements
Must have
• The logo provided
• Ability to change page contents easily
• Ability to add social media icons as needed
Nice to have
• Use of the typewriter image
Should not have
• Complicated pages that are not easily editable

```html
<!DOCTYPE html>
<html lang="en">
<head>
<meta charset="utf-8">
<title>Mara Penrith Copywriter</title>
<link href="https://fonts.googleapis.com/css2?family=Open+Sans:wght@400;600&family=Roboto+Slab:wght@300;400&display=swap" rel="stylesheet">
<style>
:root{
  --ink:#222;
  --text:#3a3a3a;
  --muted:#555;
  --accent:#c97a86;
  --blush:#fce6f1;
  --hero:#e4e4e4;
  --card:#e8e8e8;
  --panel:#efefef;
  --rule:#d6d6d6;
  --footer:#3b3b3b;
  --button:#666;
  --white:#fff;
}
*{box-sizing:border-box;margin:0;padding:0}
html,body{width:725px;height:1200px;overflow:hidden;background:var(--white)}
body{position:relative;font-family:"Open Sans",Arial,sans-serif;color:var(--text)}
.slab{font-family:"Roboto Slab",Georgia,serif}

.site-header{position:absolute;left:0;top:0;width:725px;height:66px}
.brand{position:absolute;left:80px;top:15px;font-family:"Roboto Slab",Georgia,serif;font-size:15px;font-weight:400;color:var(--ink);display:flex;align-items:center;gap:7px}
.brand-mark{width:9px;height:9px;background:var(--blush);border:0}
.contact-line{position:absolute;right:80px;top:13px;font-family:"Roboto Slab",Georgia,serif;font-weight:300;font-size:11px;color:var(--ink);display:flex;gap:18px;align-items:center}
.contact-line span{display:flex;align-items:center;gap:6px}
.main-nav{position:absolute;right:80px;top:40px;display:flex;gap:20px;font-family:"Roboto Slab",Georgia,serif;font-size:8.5px;color:var(--ink)}
.main-nav .current{color:var(--accent)}

.hero{position:absolute;left:0;top:66px;width:725px;height:247px;background:var(--hero)}
.hero h1{position:absolute;left:80px;top:78px;font-family:"Roboto Slab",Georgia,serif;font-weight:300;font-size:21px;color:var(--ink)}
.hero p{position:absolute;left:80px;top:111px;width:285px;font-size:7.4px;line-height:13.6px;color:var(--ink)}
.hero-photo{position:absolute;left:450px;top:20px;width:170px;height:227px;background:linear-gradient(180deg,#f2f2f2 0%,#3a3a3a 30%,#1b1b1b 75%,#e0e0e0 100%)}
.arrow{position:absolute}

.section-title{position:absolute;left:0;width:725px;text-align:center;font-family:"Roboto Slab",Georgia,serif;font-weight:300;font-size:20px;color:var(--ink)}
.divider{position:absolute;left:0;width:725px;height:1px;background:var(--rule)}

.service{position:absolute;top:395px;width:270px;height:97px;background:var(--blush)}
.service svg{position:absolute;left:14px;top:24px}
.service h3{position:absolute;left:80px;top:15px;font-family:"Roboto Slab",Georgia,serif;font-weight:400;font-size:14px;color:var(--ink)}
.service p{position:absolute;left:81px;top:38px;width:180px;font-size:6.2px;line-height:11.6px;color:var(--muted)}

.work{position:absolute;top:623px;width:178px;height:187px;background:var(--card)}
.work .thumb{position:absolute;left:5px;top:5px;width:168px;height:114px}
.work h3{position:absolute;left:8px;top:129px;font-family:"Roboto Slab",Georgia,serif;font-weight:400;font-size:10px;color:var(--ink)}
.work p{position:absolute;left:8px;top:148px;width:164px;font-size:6.2px;line-height:10.8px;color:var(--muted)}
.work a{color:var(--ink);font-weight:600;text-decoration:underline}

.post{position:absolute;left:80px;top:946px;width:565px;height:154px;background:var(--panel)}
.post .thumb{position:absolute;left:0;top:0;width:282px;height:154px;background:linear-gradient(120deg,#d9cfbf 0%,#b4784a 45%,#2a2a2a 80%,#6d6d6d 100%)}
.post time{position:absolute;left:317px;top:34px;font-size:9.5px;color:var(--ink)}
.post h3{position:absolute;left:317px;top:53px;width:230px;font-family:"Roboto Slab",Georgia,serif;font-weight:300;font-size:11.2px;line-height:16px;color:var(--ink)}
.post .button{position:absolute;left:317px;top:93px;width:56px;height:25px;background:var(--button);color:var(--white);font-family:"Roboto Slab",Georgia,serif;font-size:7px;display:flex;align-items:center;justify-content:center;border-radius:1px}

.site-footer{position:absolute;left:0;top:1151px;width:725px;height:49px;background:var(--footer);color:#c9c9c9;font-size:6.2px}
.footer-nav{position:absolute;left:80px;top:14px;display:flex;gap:6px}
.copyright{position:absolute;left:80px;top:30px}
.social{position:absolute;right:80px;top:12px;display:flex;gap:5px}
.social span{width:15px;height:15px;border-radius:50%}
.social .one{background:#3b5998}
.social .two{background:#1da1f2}
</style>
</head>
<body>

<header class="site-header">
  <div class="brand"><span class="brand-mark"></span>Mara Penrith Copywriter</div>
  <div class="contact-line">
    <span><svg width="9" height="9" viewBox="0 0 24 24"><path fill="#333" d="M6.6 10.8a15.1 15.1 0 0 0 6.6 6.6l2.2-2.2c.3-.3.7-.4 1-.2 1.1.4 2.3.6 3.6.6.6 0 1 .4 1 1V20c0 .6-.4 1-1 1A17 17 0 0 1 3 4c0-.6.4-1 1-1h3.5c.6 0 1 .4 1 1 0 1.3.2 2.5.6 3.6.1.3 0 .7-.2 1z"/></svg>(0412 583 906)</span>
    <span><svg width="11" height="9" viewBox="0 0 24 18"><path fill="#333" d="M0 0h24v2L12 10 0 2zM0 4.5l12 8 12-8V18H0z"/></svg>mara.penrith.copywriter@fernmail.test</span>
  </div>
  <nav class="main-nav"><span class="current">Home</span><span>Services</span><span>Portfolio</span><span>Blog</span><span>Contact</span></nav>
</header>

<section class="hero">
  <svg class="arrow" style="left:29px;top:117px" width="8" height="12" viewBox="0 0 8 12"><path d="M7 1 2 6l5 5" fill="none" stroke="#333" stroke-width="2"/></svg>
  <h1>Welcome to Mara Penrith</h1>
  <p>Fusce sollicitudin lorem et luctus volutpat. Proin placerat dapibus gravida. In tristique tristique nulla eget hendrerit. Maecenas vel tortor accumsan quam varius imperdiet vel eget elit. Aenean facilisis tincidunt lectus, id dictum nisi luctus eget. Vivamus efficitur ex condimentum, malesuada eros eget.</p>
  <div class="hero-photo" role="img" aria-label="Photo of a black vintage typewriter with a sheet of paper"></div>
  <svg class="arrow" style="left:689px;top:117px" width="8" height="12" viewBox="0 0 8 12"><path d="M1 1l5 5-5 5" fill="none" stroke="#333" stroke-width="2"/></svg>
</section>

<h2 class="section-title" style="top:355px">Services</h2>
<article class="service" style="left:82px">
  <svg width="50" height="50" viewBox="0 0 50 50" fill="none" stroke="#222" stroke-width="2"><path d="M4 8h28v38H4z"/><path d="M8 4h28v4"/><path d="M10 16h16M10 22h16M10 28h16M10 34h12"/><path d="M44 14l-12 20-2 6 5-4 12-20z"/></svg>
  <h3>Freelance Copywriter</h3>
  <p>Etiam mattis augue vehicula odio posuere, sit amet tempus. Nulla facilisi. Etiam vel massa elementum, bibendum tellus venenatis, feugiat massa. Curabitur venenatis lacinia ornare. Cras sollicitudin cursus dui eu placerat.</p>
</article>
<article class="service" style="left:375px">
  <svg width="60" height="50" viewBox="0 0 60 50" fill="none" stroke="#222" stroke-width="2.2" stroke-linejoin="round"><path d="M2 22 56 4 36 44 26 30z"/><path d="M56 4 26 30l-2 12 6-8"/></svg>
  <h3>Maecenas vel tortor</h3>
  <p>Etiam mattis augue vehicula odio posuere, sit amet tempus. Nulla facilisi. Etiam vel massa elementum, bibendum tellus venenatis, feugiat massa. Curabitur venenatis lacinia ornare. Cras sollicitudin cursus dui eu placerat.</p>
</article>

<div class="divider" style="top:540px"></div>

<h2 class="section-title" style="top:583px">Portfolio</h2>
<article class="work" style="left:80px">
  <div class="thumb" role="img" aria-label="Close-up photo of typewritten text on paper" style="background:linear-gradient(135deg,#f0f0f0 0%,#bdbdbd 50%,#2e2e2e 100%)"></div>
  <h3>Etiam mattis augue vehicula</h3>
  <p>Etiam vel massa elementum, bibendum tellus venenatis, feugiat massa. Curabitur venenatis lacinia ornare. Cras sollicitudin cursus. <a>More</a></p>
</article>
<article class="work" style="left:273px">
  <div class="thumb" role="img" aria-label="Photo of a writer working on a laptop at a wooden desk" style="background:linear-gradient(160deg,#dfe3e3 0%,#8a8f92 45%,#8a5a38 100%)"></div>
  <h3>Aliquam erat volutpat</h3>
  <p>Etiam vel massa elementum, bibendum tellus venenatis, feugiat massa. Curabitur venenatis lacinia ornare. Cras sollicitudin cursus. <a>More</a></p>
</article>
<article class="work" style="left:467px">
  <div class="thumb" role="img" aria-label="Photo of a desk with laptop, phone, notebook and coffee" style="background:linear-gradient(150deg,#c8c8c8 0%,#6b4a34 50%,#4a3526 100%)"></div>
  <h3>Pellentesque convallis molestie</h3>
  <p>Etiam vel massa elementum, bibendum tellus venenatis, feugiat massa. Curabitur venenatis lacinia ornare. Cras sollicitudin cursus. <a>More</a></p>
</article>

<div class="divider" style="top:859px"></div>

<h2 class="section-title" style="top:902px">Blog</h2>
<svg class="arrow" style="left:34px;top:1016px" width="9" height="14" viewBox="0 0 9 14"><path d="M8 1 2 7l6 6" fill="none" stroke="#333" stroke-width="2"/></svg>
<article class="post">
  <div class="thumb" role="img" aria-label="Photo of a notebook, glasses, pen and wallet on a wooden desk"></div>
  <time>22 August, 2018</time>
  <h3>Maecenas vel tortor accumsan quam varius imperdiet vel eget elit. Aenean facilisis</h3>
  <span class="button">Read More</span>
</article>
<svg class="arrow" style="left:682px;top:1016px" width="9" height="14" viewBox="0 0 9 14"><path d="M1 1l6 6-6 6" fill="none" stroke="#333" stroke-width="2"/></svg>

<footer class="site-footer">
  <nav class="footer-nav"><span>Home</span><span>|</span><span>Services</span><span>|</span><span>Portfolio</span><span>|</span><span>Blog</span><span>|</span><span>Contact</span></nav>
  <div class="copyright">Copyright © 2018 Mara Penrith. All rights reserved.</div>
  <div class="social"><span class="one"></span><span class="two"></span></div>
</footer>

</body>
</html>
```